VELK Redesign

Make a more modern looking Homepage. Our page: www.velk-example.at
Should look like:
www.tarnok-example.com/at/de/
https://web.dovrand-example.com
https://id.pallomere-example.com

Target Market(s)

furniture industry

Number of Pages Required

1 page

Font styles to use
Sans Serif

Colors
3176b5

```html
<!DOCTYPE html>
<html lang="en">
<head>
<meta charset="utf-8">
<title>VELK – Fashion for Furniture</title>
<link href="https://fonts.googleapis.com/css2?family=Lato:ital,wght@0,400;0,700;0,900;1,400&display=swap" rel="stylesheet">
<style>
:root{
  --blue:#3176b5;
  --band:#2c5ea6;
  --ink:#1d1d1d;
  --text:#555;
  --footer:#1f1f21;
  --white:#fff;
}
*{box-sizing:border-box;margin:0;padding:0}
html,body{width:1200px;height:3805px;overflow:hidden;background:#fff}
body{position:relative;font-family:'Lato',sans-serif;color:var(--ink)}
.abs{position:absolute}
.center{left:0;width:1200px;text-align:center}

/* hero */
.hero{left:0;top:0;width:1200px;height:623px;background:linear-gradient(160deg,#6a5a4c 0%,#3c3530 45%,#5d5349 75%,#2d2824 100%)}
.hero-shade{left:0;top:0;width:1200px;height:623px;background:rgba(20,18,16,.35)}
.brand{display:flex;align-items:center;gap:14px;color:var(--white)}
.brand-dot{width:44px;height:44px;border-radius:50%;background:var(--white)}
.brand-name{font-size:46px;font-weight:400;letter-spacing:4px;line-height:1}
.brand-tag{font-size:9px;letter-spacing:1px;color:var(--white)}
.pill{height:50px;border:2px solid rgba(255,255,255,.85);border-radius:25px;color:#fff;font-size:15px;font-weight:700;display:flex;align-items:center;justify-content:center;gap:6px}
.lang{color:#fff;font-size:15px;font-weight:700}
.nav{top:101px;left:478px;display:flex;gap:30px;font-size:16px;font-weight:700;color:#fff}
.nav .active{color:#6da9e6}
.hero-title{top:245px;font-size:64px;font-weight:700;color:#fff;letter-spacing:1px}
.search{left:233px;top:367px;width:595px;height:63px;background:#fff;display:flex;align-items:center;padding-left:28px;gap:18px;color:#777;font-size:16px}
.search-btn{left:828px;top:367px;width:137px;height:63px;background:var(--blue);color:#fff;font-weight:700;font-size:17px;display:flex;align-items:center;justify-content:center;letter-spacing:1px}
.dots{top:526px;left:565px;display:flex;gap:6px}
.dots span{width:14px;height:14px;border-radius:50%;border:2px solid #fff}
.dots span.on{background:#fff}

.badge{width:84px;height:84px;border-radius:50%;background:var(--blue);border:5px solid #fff;left:558px}

/* welcome */
.h2{font-size:50px;font-weight:900;color:var(--ink)}
.sub{top:810px;font-size:23px;color:var(--blue)}
.intro{left:165px;top:873px;width:870px;text-align:center;font-size:15px;line-height:29px;color:var(--text)}
.ph{}
.tile-label{font-size:26px;color:var(--ink);text-align:center}

/* testimonials */
.band{left:0;top:1923px;width:1200px;height:575px;background:var(--band)}
.quote{left:220px;top:2152px;width:760px;text-align:center;font-style:italic;color:#dfe8f5;font-size:16px;line-height:30px}
.avatar{border-radius:50%}

/* news */
.card-box{border:2px solid var(--blue);border-bottom:none;background:#fff;height:110px}
.card-title{font-size:20px;font-weight:700;text-align:center;color:var(--ink)}
.card-meta{font-size:14px;color:var(--text);text-align:center}
.card-meta b{color:var(--blue)}
.card-text{font-size:14px;line-height:25px;color:var(--text);text-align:center}
.more{font-size:14px;font-weight:900;color:var(--blue);text-align:center;letter-spacing:.5px}

/* footer */
.footer{left:0;top:3345px;width:1200px;height:460px;background:var(--footer)}
.f-head{font-size:18px;font-weight:700;color:#fff}
.f-list{font-size:14px;color:#ddd;line-height:25px;list-style:none}
.f-text{font-size:14px;color:#ddd;line-height:22px}
.email{width:252px;height:38px;background:#fff;color:#555;font-size:13px;padding:11px 10px}
.sub-btn{width:145px;height:50px;border-radius:25px;background:var(--blue);color:#fff;font-weight:700;font-size:15px;display:flex;align-items:center;justify-content:center}
.contact-row{display:flex;gap:26px;align-items:flex-start;font-size:14px;color:#ddd;line-height:20px}
.social{width:36px;height:36px;border-radius:50%;border:2px solid #bbb}
</style>
</head>
<body>

<header>
  <div class="abs hero" role="img" aria-label="Photo of a craftsman sketching furniture plans at a workshop table"></div>
  <div class="abs hero-shade"></div>
  <div class="abs" style="left:110px;top:40px">
    <div class="brand"><span class="brand-dot"></span><span class="brand-name">VELK</span></div>
    <div class="brand-tag" style="margin-left:58px;margin-top:4px">FASHION FOR FURNITURE</div>
  </div>
  <div class="abs pill" style="left:752px;top:30px;width:128px">
    <svg width="14" height="14" viewBox="0 0 14 14"><rect x="2" y="6" width="10" height="8" fill="#fff"/><path d="M4 6V4a3 3 0 0 1 6 0v2" stroke="#fff" stroke-width="2" fill="none"/></svg>LOGIN</div>
  <div class="abs pill" style="left:888px;top:30px;width:130px">
    <svg width="14" height="14" viewBox="0 0 14 14"><path d="M2 12l1-4 7-7 3 3-7 7z" fill="#fff"/></svg>REGISTER</div>
  <div class="abs lang" style="left:1038px;top:45px">ENG ▾</div>
  <nav class="abs nav"><span class="active">Home</span><span>Brand New</span><span>Catalog Configurator</span><span>Light Configurator</span><span>Lamp</span></nav>
  <h1 class="abs center hero-title">FASHION FOR FURNITURE</h1>
  <div class="abs search">
    <svg width="16" height="16" viewBox="0 0 16 16"><circle cx="6.5" cy="6.5" r="5" stroke="#222" stroke-width="2.2" fill="none"/><path d="M10 10l5 5" stroke="#222" stroke-width="2.4"/></svg>
    What are you looking for?</div>
  <div class="abs search-btn">SEARCH</div>
  <div class="abs dots"><span class="on"></span><span></span><span></span><span></span></div>
</header>
<div class="abs badge" style="top:590px"></div>

<section>
  <h2 class="abs center h2" style="top:728px">WELCOME TO VELK</h2>
  <p class="abs center sub">Furniture fittings in their most beautiful form</p>
  <p class="abs intro">The 70-year-old family business is now active as an international player in more than 50 countries. Tradition and durability combined with striving for innovation have made VELK one of the leading producers and suppliers of decorative furniture fittings. Developing the design on the pulse of time is just as much a part of VELK's daily work as developing suitable products that meet the most diverse requirements in terms of appearance and function worldwide.</p>

  <div class="abs" style="left:112px;top:1050px;width:478px;height:323px;background:linear-gradient(160deg,#d9d4cc,#8c7a66)" role="img" aria-label="Furniture showroom with customers"></div>
  <div class="abs" style="left:610px;top:1050px;width:478px;height:323px;background:linear-gradient(135deg,#f2f2f0,#c9c6c0)" role="img" aria-label="Close-up of a metal door handle on a white door"></div>
  <div class="abs tile-label" style="left:112px;top:1399px;width:478px">Catalog Configurator</div>
  <div class="abs tile-label" style="left:610px;top:1399px;width:478px">Light Configurator</div>

  <div class="abs" style="left:112px;top:1472px;width:314px;height:270px;background:linear-gradient(160deg,#cfc9c1,#8a7f74)" role="img" aria-label="Woman using a tablet in a shop"></div>
  <div class="abs" style="left:443px;top:1472px;width:314px;height:270px;background:linear-gradient(160deg,#2a3140,#b39273)" role="img" aria-label="Floor plans and wood samples on a desk"></div>
  <div class="abs" style="left:774px;top:1472px;width:314px;height:270px;background:linear-gradient(160deg,#d8d3cb,#a09484)" role="img" aria-label="Woman reviewing design papers at a table"></div>
  <div class="abs tile-label" style="left:112px;top:1768px;width:314px">Downloads</div>
  <div class="abs tile-label" style="left:443px;top:1768px;width:314px">Brand New</div>
  <div class="abs tile-label" style="left:774px;top:1768px;width:314px">Exhibition Dates</div>
</section>

<section>
  <div class="abs band"></div>
  <h2 class="abs center h2" style="top:2005px;color:#fff;font-weight:700">CLIENT TESTIMONIALS</h2>
  <svg class="abs" style="left:548px;top:2115px" width="104" height="22" viewBox="0 0 104 22">
    <g fill="#fff" stroke="#fff" stroke-width="1.2">
      <path d="M10 1l2.6 6 6.4.6-4.9 4.2 1.5 6.3L10 14.8 4.4 18.1l1.5-6.3L1 7.6l6.4-.6z"/>
      <path transform="translate(21 0)" d="M10 1l2.6 6 6.4.6-4.9 4.2 1.5 6.3L10 14.8 4.4 18.1l1.5-6.3L1 7.6l6.4-.6z"/>
      <path transform="translate(42 0)" d="M10 1l2.6 6 6.4.6-4.9 4.2 1.5 6.3L10 14.8 4.4 18.1l1.5-6.3L1 7.6l6.4-.6z"/>
      <path transform="translate(63 0)" d="M10 1l2.6 6 6.4.6-4.9 4.2 1.5 6.3L10 14.8 4.4 18.1l1.5-6.3L1 7.6l6.4-.6z"/>
      <path transform="translate(84 0)" fill="none" d="M10 1l2.6 6 6.4.6-4.9 4.2 1.5 6.3L10 14.8 4.4 18.1l1.5-6.3L1 7.6l6.4-.6z"/>
    </g>
  </svg>
  <p class="abs quote">Nemo enim ipsam voluptatem quia voluptas sit aspernatur aut odit aut fugit, sed quia consequuntur magni dolores eos qui ratione voluptatem sequi nesciunt neque porro quisquam est, qui dolorem ipsum quia dit</p>
  <div class="abs avatar" style="left:446px;top:2254px;width:84px;height:84px;background:#9aaec9" role="img" aria-label="Client portrait"></div>
  <div class="abs avatar" style="left:551px;top:2248px;width:98px;height:98px;background:#6e5a4c;border:3px solid #fff" role="img" aria-label="Client portrait"></div>
  <div class="abs avatar" style="left:670px;top:2254px;width:84px;height:84px;background:#9aaec9" role="img" aria-label="Client portrait"></div>
  <div class="abs center" style="top:2370px;font-size:17px;font-weight:700;color:#fff">MARK HALDEN</div>
  <div class="abs center" style="top:2397px;font-size:14px;color:#dfe8f5">Web Designer</div>
</section>

<section>
  <h2 class="abs center h2" style="top:2608px">LATEST NEWS</h2>

  <div class="abs" style="left:122px;top:2727px;width:290px;height:215px;background:linear-gradient(135deg,#6b2f16,#b55b2a)" role="img" aria-label="Wooden door with metal handle and letter slot"></div>
  <div class="abs" style="left:454px;top:2727px;width:290px;height:215px;background:linear-gradient(135deg,#f4f2ee,#c7a24c)" role="img" aria-label="Hand turning a brass door knob"></div>
  <div class="abs" style="left:787px;top:2727px;width:290px;height:215px;background:linear-gradient(135deg,#ddd6cc,#5a4434)" role="img" aria-label="Modern restaurant interior with chairs"></div>

  <div class="abs card-box" style="left:113px;top:2967px;width:300px"></div>
  <div class="abs card-box" style="left:446px;top:2967px;width:300px"></div>
  <div class="abs card-box" style="left:778px;top:2967px;width:302px"></div>

  <div class="abs card-title" style="left:113px;top:3004px;width:300px">Finibus Bonorum et Malor</div>
  <div class="abs card-title" style="left:446px;top:3004px;width:300px">Finibus Bonorum et Malor</div>
  <div class="abs card-title" style="left:778px;top:3004px;width:302px">Finibus Bonorum et Malor</div>

  <div class="abs card-meta" style="left:113px;top:3043px;width:300px"><b>▦</b> 08/02/2018 &nbsp;|&nbsp; <b>●</b> John Doe</div>
  <div class="abs card-meta" style="left:446px;top:3043px;width:300px"><b>▦</b> 08/02/2018 &nbsp;|&nbsp; <b>●</b> John Doe</div>
  <div class="abs card-meta" style="left:778px;top:3043px;width:302px"><b>▦</b> 08/02/2018 &nbsp;|&nbsp; <b>●</b> John Doe</div>

  <p class="abs card-text" style="left:123px;top:3081px;width:280px">Nam libero tempore, cum soluta nobis est eligendi optio cumque nihil impedique minus id quod maxime placea</p>
  <p class="abs card-text" style="left:456px;top:3081px;width:280px">Nam libero tempore, cum soluta nobis est eligendi optio cumque nihil impedique minus id quod maxime placea</p>
  <p class="abs card-text" style="left:789px;top:3081px;width:280px">Nam libero tempore, cum soluta nobis est eligendi optio cumque nihil impedique minus id quod maxime placea</p>

  <div class="abs more" style="left:113px;top:3178px;width:300px">READ MORE</div>
  <div class="abs more" style="left:446px;top:3178px;width:300px">READ MORE</div>
  <div class="abs more" style="left:778px;top:3178px;width:302px">READ MORE</div>
</section>

<footer>
  <div class="abs footer"></div>
  <div class="abs badge" style="top:3307px"></div>
  <div class="abs" style="left:110px;top:3518px">
    <div class="brand"><span class="brand-dot"></span><span class="brand-name">VELK</span></div>
    <div class="brand-tag" style="margin-left:58px;margin-top:4px">FASHION FOR FURNITURE</div>
  </div>

  <div class="abs f-head" style="left:402px;top:3462px">Information</div>
  <ul class="abs f-list" style="left:402px;top:3501px">
    <li>Help</li><li>FAQ</li><li>Support</li><li>Sitemap</li><li>Terms Of Use</li><li>Privacy Statement</li>
  </ul>

  <div class="abs f-head" style="left:585px;top:3462px">Newsletter Subscription</div>
  <p class="abs f-text" style="left:585px;top:3502px;width:250px">Register your Email Address to get information about us</p>
  <div class="abs email" style="left:585px;top:3557px">Email Address</div>
  <div class="abs sub-btn" style="left:585px;top:3612px">SUBSCRIBE</div>

  <div class="abs f-head" style="left:886px;top:3462px">Contact Us</div>
  <div class="abs" style="left:886px;top:3505px;display:flex;flex-direction:column;gap:20px">
    <div class="contact-row"><svg width="12" height="16" viewBox="0 0 12 16"><path d="M6 0a6 6 0 0 1 6 6c0 4-6 10-6 10S0 10 0 6a6 6 0 0 1 6-6z" fill="#fff"/><circle cx="6" cy="6" r="2" fill="#1f1f21"/></svg><span>Ges.mbH Lindenweg 8<br>4410 Hallmoor Austria EUROPE</span></div>
    <div class="contact-row"><svg width="12" height="14" viewBox="0 0 12 14"><path d="M2 0h3l1 4-2 1a7 7 0 0 0 3 4l1-2 4 1v3c0 1-1 3-3 3C4 14 0 8 0 3 0 1 1 0 2 0z" fill="#fff"/></svg><span>+43 (0) 5550 1200-0</span></div>
    <div class="contact-row"><svg width="12" height="14" viewBox="0 0 12 14"><rect x="0" y="3" width="12" height="10" fill="#fff"/><rect x="3" y="0" width="6" height="4" fill="#fff"/></svg><span>+43 (0) 5550 1299</span></div>
    <div class="contact-row"><svg width="12" height="14" viewBox="0 0 12 14"><rect x="0" y="3" width="12" height="9" fill="#fff"/><path d="M0 3l6 5 6-5" stroke="#1f1f21" fill="none"/></svg><span>office@velk-example.at</span></div>
  </div>

  <div class="abs" style="left:110px;top:3748px;font-size:13px;color:#ddd">Copyrights © 2019, VELK. All rights reserved.</div>
  <div class="abs social" style="left:966px;top:3740px"></div>
  <div class="abs social" style="left:1009px;top:3740px"></div>
  <div class="abs social" style="left:1052px;top:3740px"></div>
</footer>

</body>
</html>
```